Business Cards for new orthopaedic surgery practice

My husband and I are starting our own orthopaedic surgery practice. We are looking for a business card that is uniform, but one will have my name/title and the other will have his. You can just create one design with my name on it for now. But when I choose your design as the winning design I will ask that you add another copy with his name/title.

We are looking for classy, simple, elite all in one. We like dark blues/a little gold/yellow. Something that goes with our logo. We want our logo incorporated. Here is all the info you need:
Business name: RV Bone & Vitality Center
Location: 38517 North Willowmere Ave
Cedar Lakes, FL 33184
Phone: 954-218-4063
Fax: 954-582-7341
Email: info@myrvbonecare.example

Names: Lydia Vance, M.D.
Board Certified Hand and Upper Extremity Surgeon

Ebo Dansu, M.D.
Board Certified Hip & Knee Replacement/General Orthopaedic Surgeon

Can decide what you want to put on the back. Maybe a slogan:
Steady Hands. Strength That Lasts

I am just going to upload our logo. The only thing is if we select you as the winning design, the location, and phone numbers may change. We will need your help to update that once fully solidified.

Industry/Entity Type

Medical

Contact Information for Business Card

Colors
0054AA
0677BA
7BADD7
CADEEF
E8F1F8
0094D4
00A9DD
6FCCEA
C7EBF8
E9F6FB

Requirements
Must have
• class, appeal,
Should not have
• We want to air on the side of masculine if we are looking at masculine vs. feminine feel. But we still want it classy, sophisticated, and something we will love

```html
<!DOCTYPE html>
<html lang="en">
<head>
<meta charset="utf-8">
<title>RV Bone &amp; Vitality Center — Business Cards</title>
<link rel="stylesheet" href="https://fonts.googleapis.com/css2?family=Barlow:wght@400;500;700&display=swap">
<style>
  :root {
    --bg: #e9eaec;
    --paper: #ffffff;
    --navy: #1e2b5c;
    --navy-deep: #161e48;
    --navy-light: #2c3868;
    --gold: #c9a45c;
    --ink: #1b1f2a;
  }
  * { box-sizing: border-box; margin: 0; padding: 0; }
  html, body { width: 1200px; height: 800px; overflow: hidden; }
  body {
    background: var(--bg);
    font-family: "Barlow", Arial, sans-serif;
    position: relative;
  }
  .card {
    position: absolute;
    top: 102px;
    width: 340px;
    height: 596px;
    border-radius: 24px;
    box-shadow: 0 18px 40px rgba(0,0,0,0.18);
    overflow: hidden;
  }
  .card--front { left: 210px; background: var(--paper); }
  .card--back {
    left: 650px;
    background: linear-gradient(160deg, var(--navy-light) 0%, var(--navy) 45%, var(--navy-deep) 100%);
  }

  /* Front */
  .brand {
    position: absolute;
    top: 58px; left: 0; right: 0;
    display: flex; flex-direction: column; align-items: center; gap: 18px;
  }
  .brand__dot {
    width: 78px; height: 78px; border-radius: 50%;
    background: var(--navy);
  }
  .brand__name {
    font-weight: 700; font-size: 20px; color: var(--navy);
    text-align: center; line-height: 1.2; width: 220px;
  }
  .divider {
    position: absolute; top: 262px; left: 48px;
    width: 244px; height: 2px; background: var(--gold);
  }
  .details { position: absolute; top: 292px; left: 48px; right: 30px; color: var(--ink); }
  .details__name {
    font-weight: 700; font-size: 27px; color: var(--navy); letter-spacing: 0.5px;
  }
  .details__title { font-size: 17px; line-height: 1.2; margin-top: 4px; }
  .contact { list-style: none; margin-top: 28px; font-size: 17px; line-height: 1.3; }
  .address { font-style: normal; margin-top: 14px; font-size: 17px; line-height: 1.25; }

  /* Back */
  .seal {
    position: absolute; top: 150px; left: 50%;
    transform: translateX(-50%);
    width: 220px; height: 220px;
    border: 2px solid var(--gold); border-radius: 50%;
    display: flex; align-items: center; justify-content: center;
  }
  .seal__name {
    font-weight: 500; font-size: 22px; line-height: 1.25; color: #fff;
    text-align: center; width: 160px; letter-spacing: 0.5px;
  }
  .tagline {
    position: absolute; left: 34px; bottom: 40px;
    font-size: 18px; color: var(--gold); letter-spacing: 0.3px;
  }
</style>
</head>
<body>
  <section class="card card--front" aria-label="Business card front">
    <div class="brand">
      <span class="brand__dot" aria-hidden="true"></span>
      <span class="brand__name">RV Bone &amp; Vitality Center</span>
    </div>
    <div class="divider" aria-hidden="true"></div>
    <div class="details">
      <h1 class="details__name">LYDIA VANCE, M.D.</h1>
      <p class="details__title">Board Certified Hand and<br>Upper Extremity Surgeon</p>
      <ul class="contact">
        <li>954-218-4063</li>
        <li>Fax : 954-582-7341</li>
        <li>info@myrvbonecare.example</li>
      </ul>
      <address class="address">38517 North Willowmere Ave<br>Cedar Lakes, FL 33184</address>
    </div>
  </section>

  <section class="card card--back" aria-label="Business card back">
    <div class="seal">
      <span class="seal__name">RV Bone &amp; Vitality Center</span>
    </div>
    <p class="tagline">Steady Hands. Strength That Lasts</p>
  </section>
</body>
</html>
```